Design my site www.brieflyledger.com

So here is what I am thinking in terms of design:

https://plenvo.com

https://www.skyluxair.com

http://kalvex.com/harbor-plaza-tower/

I want the theme to be white and blue (royal blue). I attached a paint picture of what I would like the site to look like in terms of placing the text. Generally, what I like about the sites above is that they are simple, you can navigate easily and have some kind of idea of what's going on by looking at the center (picture and motto). Let's establish a clear understanding of how the functional part of the site would look like. Please see the picture attached.

I want to keep it simple: On top would be the Name 'BRIEFLY ledger", somewhere to the right on top on the page would be 'Sign in" button.

In the center would be a picture (maybe a video) with the Motto (on top of it all in capital) OBSERVE NAVIGATE DECIDE and below would be the "sign up now"

Below the picture (like on kalvex.com site) or to the left on top of the page would be "About Us', "Press" "Contact Us' buttons.

Then once the user gets to his page his got 3 tabs " Press Headlines", "Events", " Briefings".

we would keep the same format I only have on the site, but separate for every Tab.

I do not want the user to get distracted. I also want him to be able to access the page though mobile phone and be able to get automatic updates just like Zorvan Pings without having to sign in daily.

The landing page must be minimalist yet with business/corporate feel where users can navigate easily and a "what you see is what you get" approach. You want an image or video (personally I prefer the video.. it does capture the users attention instantly, as long as it is an interesting video), with your taglines in it.

Sections available to public: About Us, Contact Us, Landing Page with Signup Option

Private: Public Sections + User Account Page, Tabs for (Events, Press Headlines, Briefings)

Target Market(s)

PR/media monitoring/diplomatic community

Coding

Coded - Design and coding required

Number of Pages Required

1 page

Font styles to use
Serif
Sans Serif

Colors
0255a3
ec1f27

Requirements
Must have
• a simple landing page, that is user friendly.
Nice to have
• a video with the explanation of how to navigate the site
Should not have
• too many colors, graphs etc.

```html
<!DOCTYPE html>
<html lang="en">
<head>
<meta charset="utf-8">
<title>Briefly Ledger</title>
<link href="https://fonts.googleapis.com/css2?family=Roboto:ital,wght@0,300;0,400;0,500;0,700;1,300&family=Roboto+Slab:wght@500;700&display=swap" rel="stylesheet">
<style>
:root{
  --royal:#0255a3;
  --royal-deep:#0d4a91;
  --royal-light:#1f6dc0;
  --red:#ec1f27;
  --white:#ffffff;
  --ink:#3a3a3a;
  --muted:#6b6b6b;
  --page:#f1f1f1;
}
*{margin:0;padding:0;box-sizing:border-box}
html,body{width:1200px;height:819px;overflow:hidden;background:var(--page);font-family:"Roboto",sans-serif;color:var(--ink)}
.site{position:relative;width:1200px;height:819px}

/* header */
.masthead{position:absolute;left:0;top:0;width:1200px;height:92px;background:var(--white)}
.brand{position:absolute;left:98px;top:22px;display:flex;align-items:center;gap:12px}
.brand-dot{width:44px;height:44px;border-radius:50%;background:var(--red)}
.brand-name{font-family:"Roboto Slab",Georgia,serif;font-weight:500;font-size:31px;color:var(--royal);line-height:1;margin-top:4px}
.follow{position:absolute;left:726px;top:40px;display:flex;align-items:center;gap:16px;font-size:10px;color:var(--muted)}
.follow .social{width:10px;height:10px;border-radius:2px;background:var(--royal)}
.follow .social.first{background:var(--red)}
.signin{position:absolute;left:978px;top:27px;width:123px;height:38px;border-radius:19px;background:linear-gradient(var(--royal-light),var(--royal-deep));color:var(--white);font-size:12.5px;font-weight:400;display:flex;align-items:center;justify-content:center;gap:8px;text-decoration:none}

/* hero */
.hero{position:absolute;left:0;top:92px;width:1200px;height:549px;overflow:hidden}
.hero-photo{position:absolute;inset:0;background:
  linear-gradient(180deg,rgba(40,40,50,.85) 0%,rgba(70,45,50,.75) 40%,rgba(40,35,45,.8) 70%,rgba(35,35,40,.9) 100%),
  linear-gradient(90deg,#2c3542 0%,#5a3a3c 55%,#6b2e2a 100%)}
.hero-inner{position:absolute;inset:0;text-align:center;color:var(--white)}
.hero-dot{position:absolute;left:581px;top:50px;width:38px;height:38px;border-radius:50%;background:var(--white)}
.hero-title{position:absolute;left:0;right:0;top:97px;font-family:"Roboto Slab",Georgia,serif;font-weight:500;font-size:30px;line-height:1.2;color:var(--white)}
.motto{position:absolute;left:0;right:0;top:150px;font-weight:700;font-size:52px;letter-spacing:.3px;line-height:1.1}
.play{position:absolute;left:541px;top:221px}
.signup{position:absolute;left:261px;top:384px;width:677px;height:51px;border-radius:3px;background:rgba(190,190,190,.6);box-shadow:0 0 0 2px rgba(40,40,40,.5);display:flex;align-items:center}
.signup-field{flex:1;display:flex;align-items:center;gap:12px;padding-left:25px;font-size:13px;color:var(--white)}
.signup-btn{width:120px;height:49px;margin-right:1px;background:var(--white);color:var(--red);font-weight:500;font-size:15px;display:flex;align-items:center;justify-content:center;gap:12px}

/* info band */
.info{position:absolute;left:99px;top:641px;width:1002px;height:98px;display:flex;background:linear-gradient(var(--royal-light),var(--royal-deep))}
.info-item{flex:1;position:relative;border-right:1px solid rgba(0,0,0,.15)}
.info-item:last-child{border-right:0}
.info-icon{position:absolute;left:27px;top:20px;width:57px;height:57px;border:2.5px solid var(--white);border-radius:50%;display:flex;align-items:center;justify-content:center}
.info-title{position:absolute;left:108px;top:19px;font-size:16px;font-weight:500;color:var(--white)}
.info-text{position:absolute;left:108px;top:45px;font-size:11px;font-style:italic;font-weight:300;line-height:18px;color:var(--white)}

/* footer */
.footer{position:absolute;left:0;top:739px;width:1200px;height:80px}
.copyright{position:absolute;left:98px;top:30px;font-size:12.5px;font-weight:300}
.connect{position:absolute;left:818px;top:21px;display:flex;align-items:center;gap:6px;font-size:12.5px;font-weight:300}
.connect .label{margin-right:4px}
.connect .social{width:31px;height:31px;border-radius:50%;border:2px solid #a9a9a9}
.connect .social.active{border-color:var(--royal)}
</style>
</head>
<body>
<div class="site">
  <header class="masthead">
    <div class="brand"><span class="brand-dot"></span><span class="brand-name">Briefly Ledger</span></div>
    <div class="follow">FOLLOW US :
      <span class="social first"></span><span class="social"></span><span class="social"></span><span class="social"></span><span class="social"></span>
    </div>
    <a class="signin" href="#">
      <svg width="16" height="14" viewBox="0 0 16 14"><path d="M9 1h5a1 1 0 0 1 1 1v10a1 1 0 0 1-1 1H9" fill="none" stroke="#fff" stroke-width="2"/><path d="M1 5h5V2l5 5-5 5V9H1z" fill="#fff"/></svg>
      SIGN IN
    </a>
  </header>

  <section class="hero">
    <div class="hero-photo" role="img" aria-label="Dusk photograph of a suspension bridge and city skyline over the river"></div>
    <div class="hero-inner">
      <span class="hero-dot"></span>
      <div class="hero-title">Briefly Ledger</div>
      <h1 class="motto">OBSERVE NAVIGATE DECIDE</h1>
      <svg class="play" width="118" height="118" viewBox="0 0 118 118" aria-label="Play video">
        <circle cx="59" cy="59" r="57" fill="rgba(0,0,0,.2)" stroke="rgba(210,210,210,.8)" stroke-width="3"/>
        <path d="M44 34v50l40-25z" fill="rgba(215,215,215,.85)"/>
      </svg>
      <form class="signup">
        <div class="signup-field">
          <svg width="18" height="16" viewBox="0 0 18 16"><path d="M17 0L0 8l5 2 1 6 3-4 5 3z" fill="#fff"/></svg>
          Enter your E-mail Address
        </div>
        <div class="signup-btn">SIGN UP
          <svg width="8" height="12" viewBox="0 0 8 12"><path d="M1 1l5 5-5 5" fill="none" stroke="#ec1f27" stroke-width="2.5"/></svg>
        </div>
      </form>
    </div>
  </section>

  <nav class="info">
    <div class="info-item">
      <div class="info-icon"><svg width="24" height="26" viewBox="0 0 24 26"><circle cx="12" cy="7" r="6" fill="#fff"/><path d="M0 26v-4a8 8 0 0 1 8-8h8a8 8 0 0 1 8 8v4z" fill="#fff"/></svg></div>
      <div class="info-title">About Us</div>
      <p class="info-text">Sed ut perspiciatis unde omnis iste natus<br>sit voluptatem accusantium...</p>
    </div>
    <div class="info-item">
      <div class="info-icon"><svg width="28" height="24" viewBox="0 0 28 24"><path d="M16 3H4a2 2 0 0 0-2 2v15a2 2 0 0 0 2 2h15a2 2 0 0 0 2-2v-8" fill="none" stroke="#fff" stroke-width="2.5"/><path d="M23 1l4 4-12 12-5 1 1-5z" fill="#fff"/></svg></div>
      <div class="info-title">Press</div>
      <p class="info-text">Sed ut perspiciatis unde omnis iste natus<br>sit voluptatem accusantium...</p>
    </div>
    <div class="info-item">
      <div class="info-icon"><svg width="22" height="28" viewBox="0 0 22 28"><path d="M0 0h14l8 8v20H0z" fill="#fff"/><path d="M5 14h12M5 18h12M5 22h12" stroke="#1a5fae" stroke-width="2"/></svg></div>
      <div class="info-title">Contact Us</div>
      <p class="info-text">Sed ut perspiciatis unde omnis iste natus<br>sit voluptatem accusantium...</p>
    </div>
  </nav>

  <footer class="footer">
    <p class="copyright">©brieflyledger.2016 |Allrights Reserved.</p>
    <div class="connect"><span class="label">Connect With Us :</span>
      <span class="social active"></span><span class="social"></span><span class="social"></span><span class="social"></span><span class="social"></span>
    </div>
  </footer>
</div>
</body>
</html>
```